Verodex business card

Business card for sustainable investment company called "Verodex". Verodex is an exchange platform selling carbon credits between buyers and sellers. Carbon Credits are an environmental commodity for reducing global carbon emissions.

the card should obviously have our logo and the theme should be sustainability/environment mixed with a trading platform.

Contact Information for Business Card

Logo, Name, Title, Phone, Email

Colors
0054AA
0677BA
7BADD7
CADEEF
E8F1F8
0094D4
00A9DD
6FCCEA
C7EBF8
E9F6FB
00AB8E
00BBA5
67D7C9
C6EFE9
E9F9F6
59FF00
82FF00
B8FF75
E3FFCB
F4FFEA

```html
<!DOCTYPE html>
<html lang="en">
<head>
<meta charset="utf-8">
<title>Verodex business card</title>
<link rel="stylesheet" href="https://fonts.googleapis.com/css2?family=Montserrat:wght@400;500;600;700&display=swap">
<style>
  :root {
    --stage: #2b2b2d;
    --navy: #1a2c59;
    --navy-deep: #14244b;
    --ink: #2c3e5c;
    --sky: #00a9dd;
    --azure: #0677ba;
    --pale: #6fccea;
    --paper: #ffffff;
    --text: #1c1c1c;
  }
  * { margin: 0; padding: 0; box-sizing: border-box; }
  html, body {
    width: 1200px; height: 960px; overflow: hidden;
    background: var(--stage);
    font-family: "Montserrat", sans-serif;
  }
  .stage {
    width: 1200px; height: 960px;
    display: flex; flex-direction: column;
    align-items: center; justify-content: center; gap: 60px;
  }
  .card {
    position: relative;
    width: 620px; height: 354px;
    border-radius: 22px;
    overflow: hidden;
    box-shadow: 0 18px 40px rgba(0,0,0,0.45);
  }
  .card-back {
    background: linear-gradient(135deg, var(--navy) 0%, var(--navy-deep) 100%);
    display: flex; align-items: center; justify-content: center;
  }
  .brand {
    display: flex; align-items: center; gap: 18px;
  }
  .brand-mark {
    width: 40px; height: 40px; border-radius: 4px;
    background: var(--sky);
  }
  .brand-name {
    font-weight: 600; letter-spacing: 1px; line-height: 1;
  }
  .card-back .brand-name { color: var(--paper); font-size: 58px; }

  .card-front { background: var(--paper); }
  .card-front .brand {
    position: absolute; left: 130px; top: 58px;
  }
  .card-front .brand-mark { width: 46px; height: 46px; }
  .card-front .brand-name { color: var(--ink); font-size: 56px; }

  .wave { position: absolute; inset: 0; width: 620px; height: 354px; }

  .person {
    position: absolute; right: 318px; top: 140px;
    text-align: right;
  }
  .person-name {
    font-size: 21px; font-weight: 700; letter-spacing: 0.5px;
    color: var(--navy);
  }
  .person-name .first { color: var(--sky); }
  .person-title {
    font-size: 15px; font-weight: 400; color: var(--text); margin-top: 4px;
  }
  .divider {
    position: absolute; left: 318px; top: 134px;
    width: 1.5px; height: 64px; background: var(--azure);
  }
  .contacts {
    position: absolute; left: 334px; top: 132px;
    list-style: none;
  }
  .contacts li {
    display: flex; align-items: center; gap: 8px;
    font-size: 14px; color: var(--text); height: 22px;
  }
  .contacts svg { width: 15px; height: 15px; flex: none; }
</style>
</head>
<body>
<main class="stage">
  <section class="card card-back">
    <div class="brand">
      <span class="brand-mark"></span>
      <span class="brand-name">VERODEX</span>
    </div>
  </section>

  <section class="card card-front">
    <svg class="wave" viewBox="0 0 620 354" aria-hidden="true">
      <defs>
        <linearGradient id="accent" x1="0" y1="0" x2="1" y2="0">
          <stop offset="0" stop-color="#6fccea" stop-opacity="0.2"/>
          <stop offset="0.45" stop-color="#00a9dd"/>
          <stop offset="1" stop-color="#0677ba" stop-opacity="0.3"/>
        </linearGradient>
      </defs>
      <path d="M0,354 L0,318 C130,348 250,330 350,282 C450,236 530,212 620,204 L620,354 Z" fill="var(--navy)"/>
      <path d="M120,338 C250,340 330,300 420,252 C500,212 560,198 612,194" fill="none" stroke="url(#accent)" stroke-width="4" stroke-linecap="round"/>
    </svg>

    <div class="brand">
      <span class="brand-mark"></span>
      <span class="brand-name">VERODEX</span>
    </div>

    <div class="person">
      <p class="person-name"><span class="first">MARTIN</span> KELLER</p>
      <p class="person-title">Co-Founder</p>
    </div>
    <span class="divider"></span>
    <ul class="contacts">
      <li>
        <svg viewBox="0 0 16 16" aria-hidden="true"><path d="M4 1.5l2.2 3-1.3 1.4c.8 1.8 2.3 3.3 4.2 4.2l1.4-1.3 3 2.2-1.2 2.5C7 13.2 2.8 9 1.5 3.8z" fill="var(--azure)"/></svg>
        555-210-3846
      </li>
      <li>
        <svg viewBox="0 0 16 16" aria-hidden="true"><rect x="1.5" y="3.5" width="13" height="9" rx="1" fill="var(--azure)"/><path d="M2 4.5l6 4.5 6-4.5" fill="none" stroke="#fff" stroke-width="1.2"/></svg>
        info@verodex.com
      </li>
      <li>
        <svg viewBox="0 0 16 16" aria-hidden="true"><circle cx="8" cy="8" r="6.5" fill="var(--azure)"/><path d="M1.5 8h13M8 1.5c-2.5 3-2.5 10 0 13M8 1.5c2.5 3 2.5 10 0 13" fill="none" stroke="#fff" stroke-width="0.9"/></svg>
        www.verodex.com
      </li>
    </ul>
  </section>
</main>
</body>
</html>
```